Business Card Design

New business card design

Target Market(s)

Residential & Commercial Property Managers

Industry/Entity Type

Plumbing Services

Contact Information for Business Card

Name - Rowan Keddle, title - Director, Phone Number - 0431 286 517, email - rowan@tbk-plumbing.com.au, Company ABN - 73 215 904 386,

Font styles to use
Sans Serif

Colors
0054AA
0677BA
7BADD7
CADEEF
E8F1F8

```html
<!DOCTYPE html>
<html lang="en">
<head>
<meta charset="utf-8">
<title>TBK Plumbing Services — Business Card</title>
<link rel="stylesheet" href="https://fonts.googleapis.com/css2?family=Arimo:wght@400;700&display=swap">
<style>
  :root {
    --page-bg: #ededed;
    --card-white: #ffffff;
    --card-dark: #1f232b;
    --card-dark-soft: #3a404a;
    --edge-blue: #1e9be0;
    --accent-blue: #1b98df;
    --ink: #1c1f24;
    --ink-soft: #4a4d52;
    --rule: #8a8d92;
    --logo-light: #f2f4f7;
  }
  * { box-sizing: border-box; margin: 0; padding: 0; }
  html, body { width: 1200px; height: 900px; overflow: hidden; }
  body {
    background: var(--page-bg);
    font-family: "Arimo", Arial, sans-serif;
    display: flex;
    align-items: center;
    justify-content: center;
    gap: 56px;
  }
  .card {
    width: 504px;
    height: 288px;
    border-radius: 26px;
    border: 4px solid var(--edge-blue);
    position: relative;
    overflow: hidden;
    box-shadow: 0 10px 24px rgba(0,0,0,0.18);
  }
  .card--front { background: var(--card-white); }
  .card--back {
    background: var(--card-dark);
    display: flex;
    align-items: center;
    justify-content: center;
  }
  .back-pattern {
    position: absolute;
    inset: 0;
    background: linear-gradient(160deg, var(--card-dark) 0%, var(--card-dark) 45%, var(--card-dark-soft) 100%);
  }
  .wordmark {
    font-family: "Arimo", Arial, sans-serif;
    font-weight: 400;
    text-align: center;
    line-height: 1;
  }
  .front-wordmark {
    position: absolute;
    top: 44px;
    left: 200px;
    color: var(--ink);
  }
  .wordmark__name { font-size: 70px; letter-spacing: 2px; }
  .wordmark__tag { font-size: 14px; letter-spacing: 7px; margin-top: 8px; }
  .back-wordmark { position: relative; color: var(--logo-light); }
  .back-wordmark .wordmark__name { font-size: 50px; }
  .back-wordmark .wordmark__tag { font-size: 10px; letter-spacing: 5px; margin-top: 6px; }
  .contact-block {
    position: absolute;
    left: 34px;
    bottom: 42px;
    display: flex;
    align-items: stretch;
    gap: 16px;
  }
  .person { text-align: right; padding-top: 2px; }
  .person__name {
    color: var(--accent-blue);
    font-weight: 700;
    font-size: 19px;
    letter-spacing: -0.5px;
    text-transform: uppercase;
  }
  .person__title { color: var(--ink-soft); font-size: 15px; margin-top: 3px; }
  .divider { width: 1px; background: var(--rule); }
  .details { color: var(--ink-soft); font-size: 16px; line-height: 1.4; }
  .details__row { display: flex; align-items: center; gap: 6px; }
  .details__row svg { width: 13px; height: 13px; fill: var(--accent-blue); flex: none; }
  .details__label { color: var(--accent-blue); }
</style>
</head>
<body>
  <section class="card card--front" aria-label="Business card front">
    <div class="wordmark front-wordmark">
      <div class="wordmark__name">tbk</div>
      <div class="wordmark__tag">plumbing services</div>
    </div>
    <div class="contact-block">
      <div class="person">
        <div class="person__name">Rowan Keddle</div>
        <div class="person__title">Director</div>
      </div>
      <div class="divider"></div>
      <div class="details">
        <div class="details__row">
          <svg viewBox="0 0 16 16" aria-hidden="true"><path d="M3.6 1.2l2.3 2.6-1.3 1.8c.9 2 2.6 3.7 4.6 4.6l1.8-1.3 2.6 2.3-1 2.4C7 14.8 1.2 9 .8 3.2z"/></svg>
          <span>0431 286 517</span>
        </div>
        <div class="details__row">
          <svg viewBox="0 0 16 16" aria-hidden="true"><path d="M1 3h14v10H1zM2.5 4.5L8 9l5.5-4.5v-.2h-11z"/></svg>
          <span>rowan@tbk-plumbing.com.au</span>
        </div>
        <div class="details__row">
          <span class="details__label">ABN:</span><span>73 215 904 386</span>
        </div>
      </div>
    </div>
  </section>

  <section class="card card--back" aria-label="Business card back">
    <div class="back-pattern" role="img" aria-label="Embossed pattern of repeated water droplets in dark grey tones"></div>
    <div class="wordmark back-wordmark">
      <div class="wordmark__name">tbk</div>
      <div class="wordmark__tag">plumbing services</div>
    </div>
  </section>
</body>
</html>
```